Modern Business Card for Larkwell 2018

Our company assumes the best about people. We are creating an online community of entrepreneurs and business leaders who struggle with marketing their business online.

This business card should POP! We recently got a new logo and are launching a new website next month, so our business cards should make a statement that feels:
-Fresh
-Smart
-Trustworthy
-Fun

Target Market(s)

small business owners, entrepreneurs

Industry/Entity Type

Digital Marketing

Contact Information for Business Card

Dimensions: 3.5" x 2"

Font styles to use
Sans Serif

Colors
f37122
ffffff

Requirements
Must have
• We need a business card with a modern, bold design. We will use one side of the card as a lead-generation offer, so text on one side will need to fit up to 140 characters. The business card should stick to our core colors (orange, black, and white).
Nice to have
• We think a vertical "portrait" design could be interesting.
Should not have
• Should not look like a traditional business card. The round icon should stand out from a distance.

```html
<!DOCTYPE html>
<html lang="en">
<head>
<meta charset="utf-8">
<title>Larkwell Business Card</title>
<link rel="stylesheet" href="https://fonts.googleapis.com/css2?family=Roboto:wght@400;500;700&family=Roboto+Condensed:wght@500&display=swap">
<style>
  :root {
    --orange: #f26a28;
    --orange-faint: #f6dccd;
    --white: #ffffff;
    --ink: #1f1f1f;
    --grey-text: #555555;
    --backdrop: #dcdcdc;
    --card-front: #f3f3f3;
  }
  html, body {
    margin: 0;
    padding: 0;
    width: 1200px;
    height: 960px;
    overflow: hidden;
    background: var(--backdrop);
    font-family: "Roboto", Arial, sans-serif;
  }
  .stage { position: relative; width: 1200px; height: 960px; }

  .card {
    position: absolute;
    width: 600px;
    height: 343px;
    overflow: hidden;
    box-shadow: 0 6px 18px rgba(0,0,0,0.18);
  }

  /* Front */
  .card-front { left: 302px; top: 118px; background: var(--card-front); }
  .front-disc {
    position: absolute;
    left: 145px; top: 16px;
    width: 310px; height: 310px;
    border-radius: 50%;
    background: var(--orange-faint);
    opacity: 0.7;
  }
  .front-info {
    position: absolute;
    left: 0; right: 0; top: 137px;
    text-align: center;
  }
  .person-name {
    font-family: "Roboto Condensed", "Arial Narrow", sans-serif;
    font-weight: 500;
    font-size: 24px;
    color: var(--orange);
    margin: 0;
    line-height: 28px;
  }
  .person-role {
    font-size: 16px;
    color: var(--ink);
    margin: 0;
    line-height: 20px;
    letter-spacing: 0.2px;
  }
  .person-email {
    font-size: 14px;
    color: var(--grey-text);
    margin: 0;
    line-height: 18px;
  }

  /* Back */
  .card-back { left: 299px; top: 499px; background: var(--orange); }
  .brand-block {
    position: absolute;
    left: 0; width: 318px; top: 58px;
    text-align: center;
    color: var(--white);
  }
  .brand-dot {
    display: block;
    width: 36px; height: 36px;
    margin: 0 auto 14px;
    border-radius: 50%;
    background: var(--white);
  }
  .brand-name {
    font-size: 37px;
    font-weight: 700;
    letter-spacing: 3.5px;
    line-height: 38px;
    margin: 0;
  }
  .brand-tagline {
    font-size: 11px;
    font-weight: 500;
    letter-spacing: 0.8px;
    text-transform: uppercase;
    margin: 6px 0 0;
  }
  .divider {
    position: absolute;
    left: 297px; top: 24px;
    width: 1px; height: 170px;
    background: rgba(255,255,255,0.55);
  }
  .offer {
    position: absolute;
    left: 322px; top: 28px;
    width: 270px;
    color: var(--white);
  }
  .offer-headline {
    font-size: 19.5px;
    font-weight: 700;
    line-height: 21px;
    margin: 0;
  }
  .offer-body {
    font-size: 15px;
    line-height: 19.5px;
    margin: 7px 0 0;
  }
  .offer-link {
    font-size: 20px;
    font-weight: 700;
    margin: 8px 0 0;
  }
  .note-band {
    position: absolute;
    left: 0; right: 0; top: 217px;
    height: 102px;
    background: var(--white);
  }
  .note-mark {
    position: absolute;
    left: 22px; top: 14px;
    width: 74px; height: 74px;
    border-radius: 50%;
    background: var(--orange);
  }
  .note-line {
    position: absolute;
    left: 124px; width: 426px;
    height: 1px;
    background: var(--ink);
  }
  .note-line.first { top: 30px; }
  .note-line.second { top: 70px; }
</style>
</head>
<body>
<main class="stage">
  <section class="card card-front">
    <div class="front-disc" aria-hidden="true"></div>
    <div class="front-info">
      <h1 class="person-name">DANA WHITFORD</h1>
      <p class="person-role">CONTENT STRATEGY COACH</p>
      <p class="person-email">dana@larkwellnow.com</p>
    </div>
  </section>

  <section class="card card-back">
    <div class="brand-block">
      <span class="brand-dot" aria-hidden="true"></span>
      <p class="brand-name">LARKWELL</p>
      <p class="brand-tagline">Share ideas that move people</p>
    </div>
    <div class="divider" aria-hidden="true"></div>
    <div class="offer">
      <p class="offer-headline">GROW YOUR AUDIENCE.<br>BOOST YOUR REVENUE.<br>BUILD LASTING VALUE.</p>
      <p class="offer-body">Claim your free Larkwell<br>Launch Kit and our<br>growth playbook today at</p>
      <p class="offer-link">Larkwellnow.com/start</p>
    </div>
    <div class="note-band">
      <span class="note-mark" aria-hidden="true"></span>
      <span class="note-line first"></span>
      <span class="note-line second"></span>
    </div>
  </section>
</main>
</body>
</html>
```